Black Car Limousine transportation business in Naples Florida

Always stand for my reliability and RVD stands for Love, K and M are the first initials of my children's names. It should show professionalism and a dedication to customer service. We keep our clients identities private. Show our professionalism. We are Black car Black tie company. We service transportation on a reserve basis to and from residents, airports, casinos, hotels,

Target Market(s)

It is a Private car service. High end clients. Businesses, Celebrity and athletes. Service to airports, hotels, special events.

Industry/Entity Type

Business

Contact Information for Business Card

A pearl metallic or Luster card. Standard business card size. Would like the name, Company email, show we take credit cards and phone number. Currently I don't have a website but will like to add later.

Logo Text

STEADFAST RVD TRANSPORTATION

Font styles to use
Serif

Colors
eaeaea
000000

Requirements
Must have
• Must have Company email, show we take credit cards and phone number. Currently I don't have a website but will like to add later.
Nice to have
• Would like to stay with a black and white theme. Open to some color trim.
Should not have
• Open to suggestions

```html
<!DOCTYPE html>
<html lang="en">
<head>
<meta charset="utf-8">
<title>Steadfast RVD Transportation – Business Card</title>
<link rel="stylesheet" href="https://fonts.googleapis.com/css2?family=Source+Serif+4:opsz,wght@8..60,400;8..60,600;8..60,700&display=swap">
<style>
  :root {
    --page-bg: #e4e4e2;
    --card-bg: #1f2a35;
    --ink: #ffffff;
    --ink-soft: #eaeaea;
  }
  * { box-sizing: border-box; margin: 0; padding: 0; }
  html, body {
    width: 1200px;
    height: 900px;
    overflow: hidden;
    background: var(--page-bg);
    font-family: "Source Serif 4", Georgia, serif;
  }
  .card {
    position: absolute;
    background: var(--card-bg);
    color: var(--ink);
  }
  .card--front { left: 238px; top: 62px; width: 555px; height: 342px; }
  .card--back  { left: 457px; top: 518px; width: 560px; height: 343px; }

  .wordmark {
    position: absolute;
    font-weight: 700;
    color: var(--ink);
    text-align: center;
    white-space: nowrap;
    line-height: 1.15;
  }
  .wordmark__main { display: block; font-size: 23px; letter-spacing: 0.5px; }
  .wordmark__sub  { display: block; font-size: 17px; letter-spacing: 0.8px; }
  .card--front .wordmark { left: 60px; top: 140px; width: 205px; }
  .card--back  .wordmark { left: 0; top: 122px; width: 100%; }
  .card--back  .wordmark__main { font-size: 34px; }
  .card--back  .wordmark__sub  { font-size: 25px; letter-spacing: 1px; }

  .contact {
    position: absolute;
    left: 291px;
    top: 86px;
    color: var(--ink-soft);
    font-size: 14.5px;
    line-height: 20px;
  }
  .contact__name { font-size: 18px; font-weight: 600; color: var(--ink); line-height: 24px; }
  .contact__title { margin-bottom: 14px; }
  .contact__address { margin-bottom: 14px; }
  .contact__line { display: flex; align-items: center; gap: 8px; white-space: nowrap; }
  .contact__icon { width: 12px; height: 12px; flex: none; }
</style>
</head>
<body>
  <section class="card card--front" aria-label="Business card front">
    <div class="wordmark">
      <span class="wordmark__main">STEADFAST RVD</span>
      <span class="wordmark__sub">TRANSPORTATION</span>
    </div>
    <div class="contact">
      <p class="contact__name">Marcus Hale</p>
      <p class="contact__title">Managing Director</p>
      <p class="contact__address">12345, Address Goes Here<br>Country Name, 123456.</p>
      <p class="contact__line">
        <svg class="contact__icon" viewBox="0 0 12 12" aria-hidden="true"><path fill="#fff" d="M2.4 0.8l1.8 2.4-1 1.2c.6 1.5 1.8 2.7 3.3 3.3l1.2-1 2.4 1.8-.9 2.1C5 10.4 1.6 7 1.4 1.7z"/></svg>
        239-555 018 442
      </p>
      <p class="contact__line">
        <svg class="contact__icon" viewBox="0 0 12 12" aria-hidden="true"><rect x="1" y="3" width="10" height="7" fill="#fff"/><path d="M1 3l5 4 5-4" fill="none" stroke="#1f2a35" stroke-width="1"/></svg>
        ride@steadfastrvd.com
      </p>
      <p class="contact__line">
        <svg class="contact__icon" viewBox="0 0 12 12" aria-hidden="true"><rect x="0.5" y="2.5" width="11" height="7.5" rx="1" fill="#fff"/><rect x="0.5" y="4.2" width="11" height="1.5" fill="#1f2a35"/></svg>
        Major credit cards accepted
      </p>
    </div>
  </section>

  <section class="card card--back" aria-label="Business card back">
    <div class="wordmark">
      <span class="wordmark__main">STEADFAST RVD</span>
      <span class="wordmark__sub">TRANSPORTATION</span>
    </div>
  </section>
</body>
</html>
```